Exclusive beauty salon needs a price list or services booklet

I need a new very attractive flyer for my beauty salon, containing information on the different services and their prices.
In attachment you can find a pdf of the "old" one, but I'd love to have a beautifully designed new one!
I'd love to have a booklet in format 148 x 148 mm, or in US format, containing 12 or 16 pages, but if you can offer other nice looking designs they are welcome!
The services that need to come in the booklet with their prices can all be found on my website: www.atelierverano.be, starting with
Gelaatsverzorging
Wimperverlenging
Suikerontharing
Wimperlifting
Permanente Make Up
Airbrush Tanning

Target Market(s)

woman from 20 to 89 years old

Industry/Entity Type

Beauty Salon

Font styles to use
Sans Serif

Colors

Designer to choose colors to be used in the design.

Requirements
Must have
• a classy nice look, it must contain details about the services from my beauty salon and their prices, and nice pictures.
• The Names, prices and explanations of the services can easily be found on my website: www.atelierverano.be
Nice to have
• In attachment you can find the "old" price list in pdf, what I need now is a "new booklet" with the new logo and updated services price list.
• I need a very nice and attractive looking booklet, classy chique, Paris chique, looking very expensive.
Should not have
• Not too much colors, not too curly, but still feminine

```html
<!DOCTYPE html>
<html lang="nl">
<head>
<meta charset="utf-8">
<title>Prijslijst Gelaatsverzorging</title>
<link rel="stylesheet" href="https://fonts.googleapis.com/css2?family=Lora:wght@400;500&family=Poppins:wght@300;400;500&display=swap">
<style>
  :root{
    --backdrop:#c9c9c9;
    --paper:#fbfbfb;
    --paper-shade:#f1f1f1;
    --rose:#d08c98;
    --rose-soft:#dca7b0;
    --rose-band:#d9a3ac;
    --rose-light:#e9b9c1;
    --ink:#2b2b2b;
    --ink-soft:#444;
    --white:#ffffff;
  }
  *{box-sizing:border-box;margin:0;padding:0}
  html,body{width:1200px;height:900px;overflow:hidden}
  body{background:var(--backdrop);font-family:"Poppins",sans-serif;color:var(--ink)}

  .spread{position:absolute;left:40px;top:163px;width:1120px;height:574px;display:flex;
    box-shadow:0 14px 30px rgba(0,0,0,.18)}
  .page{position:relative;width:560px;height:574px;background:var(--paper);overflow:hidden}
  .page--left{background:linear-gradient(90deg,var(--paper) 80%,var(--paper-shade) 100%)}
  .page--right{background:linear-gradient(90deg,#e6e6e6 0%,var(--paper) 12%,var(--paper) 100%)}

  .photo{position:absolute;width:150px;height:150px;border-radius:50%}
  .photo--skin-a{background:radial-gradient(circle at 55% 40%,#f3dcd2,#e2bfb3 60%,#c99a8c)}
  .photo--skin-b{background:radial-gradient(circle at 60% 45%,#e8c5ad,#d7a585 55%,#f0ece9 80%)}
  .photo--skin-c{background:radial-gradient(circle at 50% 45%,#f4f0ea,#e8d6c8 55%,#d3ad98)}
  .photo--skin-d{background:radial-gradient(circle at 50% 45%,#f1d8cb,#e0baa6 55%,#c99c88)}

  .service{position:absolute;width:290px}
  .service__title{font-family:"Lora",serif;font-weight:400;font-size:17px;color:var(--rose);margin-bottom:10px}
  .service__text{font-size:8.6px;line-height:14px;font-weight:300;color:var(--ink-soft)}
  .price{display:flex;align-items:center;gap:12px;margin-top:10px}
  .price__tag{background:var(--rose-soft);color:var(--white);font-size:9px;padding:1px 10px;line-height:15px}
  .price__time{font-size:9px;color:var(--rose-light);font-weight:300}

  .band{position:absolute;left:0;top:436px;width:100%;height:111px;background:var(--rose-band);
    text-align:center;color:var(--ink)}
  .band__pattern{position:absolute;inset:0;background:linear-gradient(90deg,rgba(255,255,255,.08),rgba(255,255,255,.16),rgba(255,255,255,.08))}
  .band__content{position:relative}
  .band__title{font-family:"Lora",serif;font-weight:400;font-size:17px;margin-top:24px;margin-bottom:12px}
  .band__title--compact{margin-top:10px;margin-bottom:6px}
  .band__note{font-size:9.5px;font-weight:500;line-height:15px}
  .band__text{font-size:7.4px;font-weight:300;line-height:12px;color:#3a3a3a;padding:0 18px}
  .band .price{justify-content:center;margin-top:5px}
  .band .price__tag{background:var(--white);color:var(--rose);font-size:8.5px;line-height:13px}
  .band .price__time{color:var(--white);font-weight:400;font-size:8.5px}
</style>
</head>
<body>
<main class="spread">
  <section class="page page--left">
    <div class="photo photo--skin-a" style="left:51px;top:44px" role="img" aria-label="Portretfoto van een vrouw met verzorgde huid"></div>
    <article class="service" style="left:229px;top:66px">
      <h2 class="service__title">Cosmetische Verzorging</h2>
      <p class="service__text">Verzorging i.o.v. Dermatoloog.<br>De verzorging bestaat uit: &nbsp;oppervlakkige reiniging, verwijderen zwarte puntjes en onzuiverheden, zuiverend masker.</p>
      <div class="price"><span class="price__tag">€ 30</span></div>
    </article>

    <div class="photo photo--skin-b" style="left:51px;top:243px" role="img" aria-label="Foto van een vrouw die haar gezicht reinigt met een wattenschijfje"></div>
    <article class="service" style="left:229px;top:242px">
      <h2 class="service__title">Flash Nettoyant</h2>
      <p class="service__text">Voor een gehydrateerde en comfortabele huid.<br>Voor alle huidtypes, bij een vermoeide huid met weinig uitstraling.<br>De verzorging bestaat uit: epilatie wenkbrauwen, oppervlakkige reiniging, diepe reiniging, crememasker aangepast aan huidconditie, serum, dagcrème, handmassage.</p>
      <div class="price"><span class="price__tag">€ 15</span><span class="price__time">for 30 min</span></div>
    </article>

    <div class="band">
      <span class="band__pattern" role="img" aria-label="Zacht bloemenpatroon in roze tinten"></span>
      <div class="band__content">
        <h3 class="band__title">Verwijderen van Gerstekorrels</h3>
        <p class="band__note">De prijs is afhankelijk van de hoeveelheid.<br>Vanaf €15, afhankelijk van de hoeveelheid</p>
      </div>
    </div>
  </section>

  <section class="page page--right">
    <article class="service" style="left:49px;top:44px;width:290px">
      <h2 class="service__title">Hydratation Essentielle</h2>
      <p class="service__text">Voor een gehydrateerde, volle en frisse huid.<br>Geschikt voor alle huidtypes.<br>De verzorging bestaat uit: epilatie wenkbrauwen, oppervlakkige reiniging, diepe reiniging, verwijderen van comedonen, massage van gelaat en decolleté, instituutmasker aangepast aan huidconditie, serum, dagcrème, handmassage.</p>
      <div class="price"><span class="price__tag">€ 65</span><span class="price__time">for 60 min</span></div>
    </article>
    <div class="photo photo--skin-c" style="left:356px;top:44px" role="img" aria-label="Foto van een vrouw met gezichtsmasker en komkommerschijfjes"></div>

    <article class="service" style="left:49px;top:246px;width:290px">
      <h2 class="service__title">Pureté Essentielle</h2>
      <p class="service__text">Voor een gezonde en gezuiverde mate huid.<br>Voor gemengde tot vette huidtypes, met of zonder onzuiverheden.<br>De verzorging bestaat uit: epilatie wenkbrauwen, oppervlakkige reiniging, diepe reiniging, verwijderen van comedonen, massage van gelaat en decolleté, instituutmasker aangepast aan huidconditie, serum, dagcrème, handmassage.</p>
      <div class="price"><span class="price__tag">€ 65</span><span class="price__time">for 60 min</span></div>
    </article>
    <div class="photo photo--skin-d" style="left:356px;top:246px" role="img" aria-label="Foto van een glimlachende vrouw die haar wangen aanraakt"></div>

    <div class="band">
      <span class="band__pattern" role="img" aria-label="Zacht bloemenpatroon in roze tinten"></span>
      <div class="band__content">
        <h3 class="band__title band__title--compact">Luxe Verzorging Suprême Expérience</h3>
        <p class="band__text">Luxe gelaatsverzorging MAISON LUNE voor een herstelde, stralende huid met gladde trekken. De verzorging bestaat uit: epilatie wenkbrauwen, oppervlakkige reiniging, diepe reiniging, verwijderen van comedonen, voorbereidend masker, massage van gelaat en decolleté, instituutmasker aangepast aan huidconditie met extra anti aging actieve werkstoffen, serum, dagcrème, handmassage</p>
        <div class="price"><span class="price__tag">€ 65</span><span class="price__time">for 60 min</span></div>
      </div>
    </div>
  </section>
</main>
</body>
</html>
```